RW Framewell Inc Business cards

We need business cards using our existing logo but slightly modified. Right now the logo says RW Loadbearing Masonry. We want to keep the RW part of the design, but replace the Structural Concrete portion with "FRAMEWELL". Please see the attached file.
Ideally this would be a blank template so we can add Different Names, titles, and phone numbers later.
On the one side we want only the logo and on the other side the detail. I'm attaching an example for you to see.
Please reach out with any other questions. Our address and other details will be given out once we find a design we like.

Target Market(s)

Construction Industry

```html
<!DOCTYPE html>
<html lang="en">
<head>
<meta charset="utf-8">
<title>RW Framewell Inc – Business Cards</title>
<link rel="stylesheet" href="https://fonts.googleapis.com/css2?family=Roboto:wght@400;700;900&display=swap">
<style>
  :root {
    --brand-blue: #1f7fc6;
    --brand-blue-light: #2a8ccf;
    --paper: #ffffff;
    --ink: #333333;
    --backdrop: #a3a3a3;
  }
  * { box-sizing: border-box; margin: 0; padding: 0; }
  html, body {
    width: 1200px; height: 982px; overflow: hidden;
    background: var(--backdrop);
    font-family: "Roboto", Arial, sans-serif;
  }
  .canvas {
    position: relative; width: 1200px; height: 982px;
    display: flex; justify-content: center; align-items: center; gap: 60px;
  }
  .card {
    width: 340px; height: 580px; position: relative;
    box-shadow: 0 6px 18px rgba(0,0,0,0.25);
  }
  .card-front {
    background: linear-gradient(160deg, var(--brand-blue) 0%, var(--brand-blue-light) 55%, var(--brand-blue) 100%);
    display: flex; align-items: center; justify-content: center;
  }
  .wordmark {
    font-weight: 900; letter-spacing: 4px; line-height: 1;
  }
  .card-front .wordmark { color: var(--paper); font-size: 130px; }
  .card-back { background: var(--paper); display: flex; flex-direction: column; align-items: center; }
  .card-back .wordmark { color: var(--brand-blue); font-size: 130px; margin-top: 70px; }
  .name-band {
    margin-top: 60px; width: 100%; height: 92px; background: var(--brand-blue);
    color: var(--paper); text-align: center;
    display: flex; flex-direction: column; justify-content: center;
  }
  .person-name { font-weight: 700; font-size: 21px; letter-spacing: 0.5px; }
  .person-title { font-size: 13px; margin-top: 4px; }
  .contact-icons { display: flex; gap: 4px; margin-top: 30px; }
  .icon-dot {
    width: 22px; height: 22px; border-radius: 50%; background: var(--brand-blue);
    display: flex; align-items: center; justify-content: center;
  }
  .contact-list { list-style: none; text-align: center; color: var(--ink); font-size: 15px; line-height: 21px; margin-top: 10px; }
  .location-icon { margin-top: 20px; }
  .address { color: var(--ink); font-size: 15px; line-height: 19px; text-align: center; margin-top: 10px; }
</style>
</head>
<body>
<main class="canvas">
  <section class="card card-front" aria-label="Card front">
    <span class="wordmark">RW</span>
  </section>

  <section class="card card-back" aria-label="Card back">
    <span class="wordmark">RW</span>
    <div class="name-band">
      <div class="person-name">DANIEL MORROW</div>
      <div class="person-title">Owner/CEO</div>
    </div>

    <div class="contact-icons">
      <span class="icon-dot"><svg width="12" height="12" viewBox="0 0 12 12"><rect x="3.5" y="1" width="5" height="10" rx="1" fill="none" stroke="#fff" stroke-width="1.2"/></svg></span>
      <span class="icon-dot"><svg width="12" height="12" viewBox="0 0 12 12"><path d="M2 2.5 L4 1.5 L5.5 4 L4.3 5 Q5.5 7.2 7 7.7 L8 6.5 L10.5 8 L9.5 10 Q5 10 2 2.5Z" fill="#fff"/></svg></span>
      <span class="icon-dot"><svg width="12" height="12" viewBox="0 0 12 12"><rect x="1.5" y="3" width="9" height="6.5" fill="#fff"/><path d="M1.5 3 L6 7 L10.5 3" fill="none" stroke="#1f7fc6" stroke-width="1"/></svg></span>
      <span class="icon-dot"><svg width="12" height="12" viewBox="0 0 12 12"><circle cx="6" cy="6" r="4.5" fill="none" stroke="#fff" stroke-width="1.2"/><path d="M1.5 6 H10.5 M6 1.5 Q3.5 6 6 10.5 M6 1.5 Q8.5 6 6 10.5" fill="none" stroke="#fff" stroke-width="0.9"/></svg></span>
    </div>

    <ul class="contact-list">
      <li>555-201-4830</li>
      <li>555-309-7162</li>
      <li>info@rwframewell.com</li>
      <li>www.rwframewell.com</li>
    </ul>

    <span class="icon-dot location-icon"><svg width="12" height="12" viewBox="0 0 12 12"><path d="M6 11 Q2 6.5 2 4.5 A4 4 0 0 1 10 4.5 Q10 6.5 6 11Z" fill="#fff"/><circle cx="6" cy="4.5" r="1.5" fill="#1f7fc6"/></svg></span>
    <p class="address">1480 W Harlow Avenue County<br>Name 7420</p>
  </section>
</main>
</body>
</html>
```